A ebook cover to reinvent the imagery of vegetable companion gardening

We needs a ebook design with illustrates minimal as well as clear and concise relevance to vegetable companion gardening . we will add a mock up design and other existing designs to help you gauge and create the sort of illustration fit for our aims.
Book Title: Orchard and Greens 202 – Garden Partner Sowing
Subtitle: Partner Handbook On Raising Crops Through Basic, Natural & Lasting Plot Methods
(Perfect For Beginners)
Author: Amber Hollow
Size: 5.5 x 8.5

```html
<!DOCTYPE html>
<html lang="en">
<head>
<meta charset="utf-8">
<title>Orchard and Greens 202 – Garden Partner Sowing</title>
<link rel="stylesheet" href="https://fonts.googleapis.com/css2?family=Bebas+Neue&family=Kaushan+Script&family=Poppins:ital,wght@0,400;0,600;0,700;1,500&display=swap">
<style>
  :root {
    --page: #ffffff;
    --paper: #f3f4f0;
    --sun: #fbbd32;
    --forest: #2f5b3c;
    --sprout: #a9c75a;
    --ink: #3a3a3a;
    --produce-red: #d9342b;
    --produce-violet: #a8507a;
    --produce-green: #5f9a3a;
  }
  * { margin: 0; padding: 0; box-sizing: border-box; }
  html, body { width: 1200px; height: 2400px; overflow: hidden; background: var(--page); }
  .cover {
    position: absolute; left: 40px; top: 332px;
    width: 1120px; height: 1735px;
    background: var(--paper);
    box-shadow: 0 10px 40px rgba(0,0,0,0.25);
    overflow: hidden;
  }
  .cover-lines { position: absolute; inset: 0; width: 1120px; height: 1735px; }
  .title-top {
    position: absolute; left: 0; right: 0; top: 200px;
    text-align: center;
    font-family: "Bebas Neue", "Oswald", sans-serif;
    font-size: 236px; line-height: 1; color: var(--sun);
  }
  .title-script {
    position: absolute; left: 0; right: 0; top: 370px;
    text-align: center;
    font-family: "Kaushan Script", cursive;
    font-size: 200px; line-height: 1; color: var(--forest);
  }
  .title-number {
    position: absolute; left: 690px; top: 505px;
    font-family: "Poppins", sans-serif; font-style: italic; font-weight: 500;
    font-size: 180px; line-height: 1; color: var(--sprout);
  }
  .ribbon-text {
    position: absolute; left: 164px; width: 793px; top: 833px; height: 100px;
    display: flex; align-items: center; justify-content: center;
    font-family: "Bebas Neue", "Oswald", sans-serif;
    font-size: 72px; line-height: 1; color: var(--forest);
  }
  .produce-photo {
    position: absolute; left: 38px; top: 979px; width: 1045px; height: 437px;
    border-radius: 45% 45% 12% 12% / 40% 40% 10% 10%;
    background: linear-gradient(90deg, var(--produce-green) 0%, var(--produce-red) 22%, var(--produce-violet) 45%, var(--produce-green) 65%, var(--produce-red) 85%, var(--produce-green) 100%);
    opacity: 0.85;
  }
  .subtitle {
    position: absolute; left: 0; right: 0; top: 1462px;
    text-align: center;
    font-family: "Poppins", sans-serif; font-weight: 600;
    font-size: 29px; line-height: 36px; color: var(--ink);
  }
  .subtitle .audience { display: block; font-weight: 400; }
  .author {
    position: absolute; left: 0; right: 0; top: 1582px;
    text-align: center;
    font-family: "Poppins", sans-serif; font-weight: 700;
    font-size: 66px; line-height: 1; letter-spacing: 0.16em; color: var(--sprout);
  }
</style>
</head>
<body>
  <main class="cover">
    <svg class="cover-lines" viewBox="0 0 975 1510" aria-hidden="true">
      <path class="frame-arc" d="M248,0 C80,100 20,260 28,390 C40,600 260,735 489,735 C720,735 945,600 951,390 C955,250 880,110 733,0" fill="none" stroke="var(--sprout)" stroke-width="5"/>
      <path class="swoosh" d="M95,541 C260,527 450,520 603,528 L603,533 C450,528 260,534 95,547 Z" fill="var(--forest)"/>
      <path class="swoosh-tip" d="M73,548 C85,532 100,528 115,530 C104,540 92,548 73,548 Z" fill="var(--forest)"/>
      <polygon class="ribbon" points="143,725 833,725 810,768 833,812 143,812 166,768" fill="var(--sun)"/>
    </svg>

    <h1 class="title">
      <span class="title-top">ORCHARD &amp;</span>
      <span class="title-script">Greens</span>
      <span class="title-number">202</span>
    </h1>

    <h2 class="ribbon-text">GARDEN PARTNER SOWING</h2>

    <div class="produce-photo" role="img" aria-label="Photograph of fresh produce: red bell pepper, red onions, spring onions, sliced cucumber, spinach leaves and cherry tomatoes"></div>

    <p class="subtitle">
      Partner Handbook On Raising Crops Through<br>
      Basic, Natural &amp; Lasting Plot Methods
      <span class="audience">(Perfect For Beginners)</span>
    </p>

    <p class="author">AMBER HOLLOW</p>
  </main>
</body>
</html>
```